Company web site

Looking for a full responsive(mobile friendly) wordpress implementation

Some material is in the website -- brelvanto.wordpress.com

But looking for a template more consistent with the logo design, and more future looking.

Target Market(s)

Enterprise Clients

Industry/Entity Type

It Company

Font styles to use
Sans Serif

Colors
33a6d7
0255a3
0455a3
cfdeed
85abd2
3176b5

Requirements
Must have
• about, contact information, partner page, success stories, customer testimonials. links to social presence.
• pricing information

```html
<!DOCTYPE html>
<html lang="en">
<head>
<meta charset="utf-8">
<title>Brelvanto — Bridging Connected Devices With Enterprise Solutions</title>
<link href="https://fonts.googleapis.com/css2?family=Lato:ital,wght@0,400;0,700;1,400&family=Play:wght@400;700&family=Roboto+Condensed:wght@300;400&display=swap" rel="stylesheet">
<style>
:root{
  --blue:#2ea3da;
  --blue-dark:#0255a3;
  --blue-light:#9fd3ec;
  --ink:#333;
  --heading:#555;
  --text:#444;
  --grey-bg:#efefef;
  --grey-ring:#5f5f5f;
  --rule:#c9c9c9;
  --footer:#1b2130;
  --footer-text:#c8ccd4;
  --white:#fff;
}
*{box-sizing:border-box;margin:0;padding:0}
html,body{width:1200px;height:3072px;overflow:hidden;background:var(--white)}
body{font-family:"Lato",sans-serif;color:var(--text);position:relative}
section,header,footer{position:relative;width:1200px}
.abs{position:absolute}
.section-title{font-family:"Play",sans-serif;font-weight:400;font-size:36px;color:var(--heading);text-align:center;position:absolute;left:0;width:1200px}
.section-title em{font-style:normal;color:var(--blue)}
.title-rule{position:absolute;height:2px;background:var(--rule)}

/* header */
.site-header{height:121px;background:var(--white)}
.brand{left:98px;top:38px;display:flex;align-items:center;gap:12px;font-family:"Play",sans-serif;font-weight:700;font-size:34px;color:var(--blue)}
.brand-dot{width:22px;height:22px;border-radius:50%;background:var(--blue)}
.top-contact{top:12px;display:flex;align-items:center;gap:14px;font-size:16px;color:var(--ink)}
.top-contact .sq{width:32px;height:32px;background:var(--blue);border-radius:3px;display:flex;align-items:center;justify-content:center}
.main-nav{top:88px;right:98px;display:flex;gap:44px;font-size:15px;font-weight:700;color:#444}
.main-nav a{color:inherit;text-decoration:none;position:relative}
.main-nav a.active{color:var(--blue)}
.main-nav a.active::after{content:"";position:absolute;left:0;right:0;bottom:-8px;height:3px;background:var(--blue)}

/* hero */
.hero{height:530px;background:radial-gradient(ellipse at 70% 40%,#33506f 0%,#16263b 45%,#0b1422 100%)}
.hero-title{position:absolute;left:0;width:1200px;top:388px;text-align:center;font-family:"Roboto Condensed",sans-serif;font-weight:400;font-size:41px;color:var(--white)}
.hero-dots{position:absolute;top:484px;left:0;width:1200px;display:flex;justify-content:center;gap:6px}
.hero-dots span{width:11px;height:11px;border-radius:50%;background:#2a3648}
.hero-dots span.on{background:var(--blue);box-shadow:0 0 0 2px #cfe8f5}

/* welcome */
.welcome{height:416px}
.welcome h1{font-family:"Play",sans-serif;font-weight:400;font-size:36px;color:var(--heading);left:98px;top:42px}
.welcome h1 em{font-style:normal;color:var(--blue)}
.welcome .rule{left:98px;top:104px;width:557px;height:2px;background:var(--rule)}
.welcome p{left:98px;width:557px;font-size:15px;line-height:22px;color:var(--ink)}
.btn{display:inline-block;background:var(--blue);color:var(--white);font-weight:700;font-size:15px;padding:10px 20px;text-decoration:none}
.video{left:698px;top:53px;width:404px;height:295px;background:linear-gradient(135deg,#a7a49f,#6d6660 55%,#3a3633);box-shadow:0 6px 12px rgba(0,0,0,.35)}

/* how it works */
.how{height:530px;background:var(--grey-bg)}
.step{position:absolute;top:154px;width:210px;text-align:center}
.step svg{display:block;margin:0 auto}
.step h3{font-size:21px;font-weight:700;color:var(--ink);margin-top:20px}
.step ul{list-style:none;font-size:15px;line-height:26px;color:var(--ink);margin-top:6px}
.step ul li::before{content:"• "}
.step ul li.more::before{content:""}
.op{position:absolute;top:195px;font-size:40px;color:var(--blue);font-weight:700;width:40px;text-align:center}

/* lifecycle */
.lifecycle{height:471px}
.lc-label{position:absolute;width:160px;text-align:center;font-size:16px;color:var(--ink)}

/* testimonials */
.testimonials{height:412px;background:var(--grey-bg)}
.quote{left:160px;width:880px;top:116px;text-align:center;font-style:italic;font-size:15px;line-height:29px;color:var(--ink)}
.quote .qm{font-family:"Play",sans-serif;color:#bbb;font-size:22px;font-style:normal;line-height:0}
.avatar{position:absolute;border-radius:50%;background:radial-gradient(circle at 50% 40%,#d9b9a0,#8d6e5c);border:3px solid #ddd}
.avatar.active{border:4px solid var(--blue)}
.person-name{left:0;width:1200px;top:359px;text-align:center;font-size:14px;font-weight:700;color:#555}

/* partners */
.partners{height:244px}
.partner-box{position:absolute;top:117px;width:144px;height:74px;border:1px solid #cfcfcf;display:flex;align-items:center;justify-content:center}
.partner-mark{width:86px;height:22px;background:#cfd3d8;border-radius:3px}
.round-arrow{position:absolute;top:132px;width:42px;height:42px;border-radius:50%;background:#f3f3f3;border:1px solid #ccc;display:flex;align-items:center;justify-content:center}

/* footer */
.site-footer{height:307px;background:var(--footer);color:var(--footer-text)}
.foot-h{position:absolute;top:38px;font-size:18px;font-weight:700;color:var(--white)}
.foot-h em{font-style:normal;color:var(--blue)}
.foot-rule{position:absolute;top:72px;height:1px;background:#3a4354}
.quick-links{left:100px;top:92px;list-style:none;font-size:12px;line-height:31px}
.quick-links li::before{content:"• "}
.quick-links li.on{color:var(--blue)}
.contact-block{left:328px;top:92px;font-size:13px;line-height:18px;width:200px}
.contact-row{display:flex;align-items:center;gap:12px;font-size:13px;margin-top:16px}
.map{left:569px;top:90px;width:299px;height:172px;background:linear-gradient(135deg,#e8e6e1,#d7d9dc 60%,#cfd8e2)}
.foot-brand{left:900px;width:250px;top:132px;text-align:center;font-family:"Play",sans-serif;font-weight:700;font-size:28px;color:#8b919c;line-height:34px}
.socials{left:900px;width:250px;top:186px;height:24px;display:flex;justify-content:center;gap:8px}
.socials span{width:24px;height:24px;border-radius:50%;background:var(--blue);flex:none}
.copyright{height:41px;background:var(--blue);color:var(--white);font-size:13px;text-align:center;line-height:41px}
</style>
</head>
<body>

<header class="site-header">
  <div class="abs brand"><span class="brand-dot"></span>Brelvanto</div>
  <div class="abs top-contact" style="left:690px">
    <span class="sq"><svg width="16" height="16" viewBox="0 0 24 24"><path fill="#fff" d="M6.6 10.8a15.1 15.1 0 0 0 6.6 6.6l2.2-2.2c.3-.3.7-.4 1-.2 1.1.4 2.3.6 3.6.6.6 0 1 .4 1 1V20c0 .6-.4 1-1 1A17 17 0 0 1 3 4c0-.6.4-1 1-1h3.5c.6 0 1 .4 1 1 0 1.3.2 2.5.6 3.6.1.3 0 .7-.2 1z"/></svg></span>
    +1-(888) 555-0142
  </div>
  <div class="abs top-contact" style="left:908px">
    <span class="sq"><svg width="16" height="16" viewBox="0 0 24 24"><path fill="#fff" d="M3 5h18v14H3z"/><path fill="none" stroke="#2ea3da" stroke-width="2" d="M3 6l9 7 9-7"/></svg></span>
    info@brelvanto.com
  </div>
  <nav class="abs main-nav">
    <a class="active" href="#">Home</a><a href="#">About</a><a href="#">Partner</a><a href="#">Success Stories</a><a href="#">Customer Testimonials</a><a href="#">Contact</a>
  </nav>
</header>

<section class="hero" role="img" aria-label="Night view of the globe from space overlaid with a web of connection lines">
  <h2 class="hero-title">Bridging Connected Devices With Enterprise Solutions</h2>
  <div class="hero-dots"><span class="on"></span><span></span><span></span><span></span></div>
</section>

<section class="welcome">
  <h1 class="abs">Welcome To <em>Brelvanto</em></h1>
  <div class="abs rule"></div>
  <p class="abs" style="top:120px">Lorem ipsum dolor sit amet, consectetuer adipiscing elit, sed diam nonummy nibh euismod tincidunt ut laoreet dolore magna aliquam erat volutpat.</p>
  <p class="abs" style="top:172px">Lorem ipsum dolor sit amet, consectetuer adipiscing elit, sed diam nonummy nibh euismod tincidunt ut laoreet dolore magna aliquam erat volutpat. Ut wisi enim ad minim veniam, quis nostrud exerci tation ullamcorper suscipit lobortis nisl ut aliquip ex ea commodo consequat. Duis autem vel eum iriure dolor in hendrerit in vulputate velit esse molestie consequat, vel illum dolore eu feugiat nulla facilisis at vero eros et accumsan et iusto.</p>
  <a class="abs btn" href="#" style="left:98px;top:325px">Learn More</a>
  <div class="abs video" role="img" aria-label="Video player showing a business team meeting around a laptop"></div>
</section>

<section class="how">
  <h2 class="section-title" style="top:44px">How It <em>Works</em></h2>
  <div class="title-rule" style="left:476px;width:248px;top:106px"></div>

  <svg width="0" height="0" style="position:absolute">
    <defs>
      <path id="cloud" d="M30 92 C8 92 6 62 26 58 C22 30 52 18 66 36 C74 8 118 10 120 44 C142 44 146 76 130 86" fill="none" stroke="#9fd3ec" stroke-width="11" stroke-linecap="round"/>
    </defs>
  </svg>

  <div class="step" style="left:59px">
    <svg width="150" height="115" viewBox="0 0 150 115"><use href="#cloud"/>
      <circle cx="104" cy="62" r="9" fill="#444"/>
      <path d="M86 80h36v24H86z" fill="#444"/><path d="M104 80v24" stroke="#fff" stroke-width="2"/></svg>
    <h3>Learn</h3>
    <ul><li>Properties</li><li>Actions</li><li>Events</li></ul>
  </div>
  <div class="op" style="left:289px">+</div>

  <div class="step" style="left:350px">
    <svg width="150" height="115" viewBox="0 0 150 115"><use href="#cloud"/>
      <g fill="none" stroke="#444" stroke-width="8" stroke-linecap="round">
        <rect x="76" y="62" width="30" height="18" rx="9" transform="rotate(-45 91 71)"/>
        <rect x="96" y="82" width="30" height="18" rx="9" transform="rotate(-45 111 91)"/>
      </g></svg>
    <h3>Connect</h3>
    <ul><li>Skyline IoT</li><li>Cobalt IoT</li><li>Linkpoint</li><li>Meshlane</li><li>Thingbase</li><li class="more">... and others</li></ul>
  </div>
  <div class="op" style="left:580px">+</div>

  <div class="step" style="left:640px">
    <svg width="150" height="115" viewBox="0 0 150 115"><use href="#cloud"/>
      <circle cx="94" cy="88" r="12" fill="none" stroke="#444" stroke-width="8" stroke-dasharray="5 3"/>
      <circle cx="94" cy="88" r="4" fill="#444"/>
      <circle cx="118" cy="64" r="8" fill="none" stroke="#444" stroke-width="6" stroke-dasharray="4 3"/></svg>
    <h3>Integrate</h3>
    <ul><li>CRM systems</li><li>HelpDeskly</li><li>Social login</li><li>Rule engine</li><li>Billing</li><li class="more">... and many others</li></ul>
  </div>
  <div class="op" style="left:875px">=</div>

  <div class="step" style="left:903px">
    <svg width="150" height="115" viewBox="0 0 150 115"><use href="#cloud"/>
      <g stroke="#444" stroke-width="4"><path d="M104 78L84 60M104 78L126 60M104 78L86 100M104 78L124 100M104 78L104 54"/></g>
      <g fill="#444"><circle cx="104" cy="78" r="8"/><circle cx="84" cy="60" r="5"/><circle cx="126" cy="60" r="5"/><circle cx="86" cy="100" r="5"/><circle cx="124" cy="100" r="5"/><circle cx="104" cy="54" r="5"/></g></svg>
    <h3>Connected<br>Product</h3>
  </div>
</section>

<section class="lifecycle">
  <h2 class="section-title" style="top:34px">End-to-end Product <em>Lifecycle Management</em></h2>
  <div class="title-rule" style="left:182px;width:836px;top:92px"></div>

  <div class="lc-label" style="left:104px;top:128px">Manufacture</div>
  <div class="lc-label" style="left:381px;top:128px">Provision</div>
  <div class="lc-label" style="left:658px;top:128px">Support</div>
  <div class="lc-label" style="left:936px;top:128px">Maintain</div>
  <div class="lc-label" style="left:242px;top:362px">Sell</div>
  <div class="lc-label" style="left:519px;top:362px">Use</div>
  <div class="lc-label" style="left:797px;top:362px">Monetize</div>

  <svg class="abs" style="left:0;top:0" width="1200" height="471" viewBox="0 0 1200 471">
    <g fill="#2ea3da">
      <circle cx="184" cy="180" r="12"/><circle cx="461" cy="180" r="12"/><circle cx="739" cy="180" r="12"/><circle cx="1016" cy="180" r="12"/>
    </g>
    <g fill="#555">
      <circle cx="322" cy="410" r="12"/><circle cx="600" cy="410" r="12"/><circle cx="877" cy="410" r="12"/>
    </g>
    <g fill="none" stroke="#fff" stroke-width="2.5">
      <path d="M182 175l5 5-5 5M459 175l5 5-5 5M737 175l5 5-5 5M1014 175l5 5-5 5M320 405l5 5-5 5M598 405l5 5-5 5M875 405l5 5-5 5"/>
    </g>
    <g fill="none" stroke-width="30">
      <path d="M99 276 H115 A69 69 0 0 0 253 276" stroke="#2ea3da"/>
      <path d="M253 276 A69 69 0 0 1 392 276" stroke="#5f5f5f"/>
      <path d="M392 276 A69 69 0 0 0 530 276" stroke="#2ea3da"/>
      <path d="M530 276 A69 69 0 0 1 669 276" stroke="#5f5f5f"/>
      <path d="M669 276 A69 69 0 0 0 808 276" stroke="#2ea3da"/>
      <path d="M808 276 A69 69 0 0 1 946 276" stroke="#5f5f5f"/>
      <path d="M946 276 A69 69 0 0 0 1085 276 H1101" stroke="#2ea3da"/>
    </g>
    <g fill="#fff" stroke="#d5d5d5" stroke-width="3">
      <circle cx="184" cy="276" r="53"/><circle cx="322" cy="276" r="53"/><circle cx="461" cy="276" r="53"/><circle cx="600" cy="276" r="53"/><circle cx="739" cy="276" r="53"/><circle cx="877" cy="276" r="53"/><circle cx="1016" cy="276" r="53"/>
    </g>
    <!-- manufacture: gears -->
    <g fill="#555"><circle cx="178" cy="282" r="14"/><circle cx="196" cy="264" r="9"/></g>
    <g fill="none" stroke="#555" stroke-width="5" stroke-dasharray="4 4"><circle cx="178" cy="282" r="18"/><circle cx="196" cy="264" r="12"/></g>
    <g fill="#fff"><circle cx="178" cy="282" r="5"/><circle cx="196" cy="264" r="3"/></g>
    <!-- sell: hand with box -->
    <rect x="308" y="250" width="28" height="24" fill="#555"/>
    <path d="M294 290 q14 -10 30 0 h22 q6 0 6 6 h-30" fill="none" stroke="#555" stroke-width="4"/>
    <!-- provision: cloud play -->
    <path d="M442 292 a14 14 0 0 1 4 -27 a18 18 0 0 1 34 6 a11 11 0 0 1 2 21" fill="none" stroke="#555" stroke-width="5"/>
    <circle cx="465" cy="290" r="14" fill="none" stroke="#555" stroke-width="4"/><path d="M461 283 l10 7 -10 7z" fill="#555"/>
    <!-- use: card -->
    <path d="M594 262h36l-6 28h-36z" fill="none" stroke="#555" stroke-width="5" stroke-linejoin="round"/>
    <path d="M568 268h16M570 276h12M572 284h10" stroke="#555" stroke-width="4"/>
    <!-- support: headset -->
    <circle cx="739" cy="264" r="13" fill="#555"/><path d="M715 304 q24 -30 48 0z" fill="#555"/>
    <path d="M722 266 a17 17 0 0 1 34 0" fill="none" stroke="#555" stroke-width="4"/>
    <!-- monetize: hand with coin -->
    <circle cx="882" cy="266" r="11" fill="none" stroke="#555" stroke-width="4"/>
    <path d="M854 292 h18 l14 -6 q10 -2 12 4 l-22 10 h-22" fill="none" stroke="#555" stroke-width="4"/>
    <!-- maintain: clipboard plus -->
    <rect x="998" y="255" width="30" height="38" rx="3" fill="none" stroke="#555" stroke-width="4"/>
    <path d="M1004 268l4 4 6-7M1004 282l4 4 6-7" fill="none" stroke="#555" stroke-width="3"/>
    <circle cx="1028" cy="292" r="11" fill="#555"/><path d="M1028 286v12M1022 292h12" stroke="#fff" stroke-width="3"/>
  </svg>
</section>

<section class="testimonials">
  <h2 class="section-title" style="top:34px">Client <em>Testimonials</em></h2>
  <div class="title-rule" style="left:440px;width:320px;top:92px"></div>
  <p class="abs quote"><span class="qm">“</span> Lorem ipsum dolor sit amet, consectetuer adipiscing elit, sed diam nonummy nibh euismod tincidunt ut laoreet dolore magna aliquam erat volutpat. Lorem ipsum dolor sit amet, consectetuer adipiscing elit, seiam nonummy nibh euismod tincidunt ut laoreet dolore magna aliquam volutpat sed diam nonummy nibh euismod. <span class="qm">”</span></p>
  <svg class="abs" style="left:336px;top:214px" width="528" height="14" viewBox="0 0 528 14"><path d="M0 2H254l10 10 10-10H528" fill="none" stroke="#aaa" stroke-width="2"/><path d="M256 2h16l-8 8z" fill="#777"/></svg>
  <svg class="abs" style="left:396px;top:278px" width="24" height="40" viewBox="0 0 24 40"><path d="M20 2L4 20l16 18" fill="none" stroke="#c8c8c8" stroke-width="3"/></svg>
  <svg class="abs" style="left:780px;top:278px" width="24" height="40" viewBox="0 0 24 40"><path d="M4 2l16 18L4 38" fill="none" stroke="#c8c8c8" stroke-width="3"/></svg>
  <div class="avatar" role="img" aria-label="Client portrait" style="left:451px;top:256px;width:82px;height:82px"></div>
  <div class="avatar active" role="img" aria-label="Client portrait" style="left:554px;top:251px;width:92px;height:92px"></div>
  <div class="avatar" role="img" aria-label="Client portrait" style="left:666px;top:256px;width:82px;height:82px"></div>
  <div class="abs person-name">Miss. Lena Varga</div>
</section>

<section class="partners">
  <h2 class="section-title" style="top:28px">Our <em>Partners</em></h2>
  <div class="title-rule" style="left:448px;width:304px;top:88px"></div>
  <div class="round-arrow" style="left:32px"><svg width="14" height="16" viewBox="0 0 14 16"><path d="M11 1L3 8l8 7" fill="none" stroke="#333" stroke-width="3"/></svg></div>
  <div class="partner-box" style="left:98px"><span class="partner-mark"></span></div>
  <div class="partner-box" style="left:270px"><span class="partner-mark"></span></div>
  <div class="partner-box" style="left:442px"><span class="partner-mark"></span></div>
  <div class="partner-box" style="left:614px"><span class="partner-mark"></span></div>
  <div class="partner-box" style="left:786px"><span class="partner-mark"></span></div>
  <div class="partner-box" style="left:958px"><span class="partner-mark"></span></div>
  <div class="round-arrow" style="left:1124px"><svg width="14" height="16" viewBox="0 0 14 16"><path d="M3 1l8 7-8 7" fill="none" stroke="#333" stroke-width="3"/></svg></div>
</section>

<footer class="site-footer">
  <h4 class="foot-h" style="left:100px">Quick <em>Links</em></h4>
  <div class="foot-rule" style="left:100px;width:140px"></div>
  <ul class="abs quick-links">
    <li class="on">Home</li><li>About</li><li>Partner</li><li>Success Stories</li><li>Customer Testimonials</li><li>Contact</li>
  </ul>

  <h4 class="foot-h" style="left:328px">Contact <em>Details</em></h4>
  <div class="foot-rule" style="left:328px;width:190px"></div>
  <div class="abs contact-block">
    <div style="color:#fff;font-size:14px">Brelvanto</div>
    <div>4810 Marlow Ave</div>
    <div>Fairhaven, CA 95120</div>
    <div class="contact-row"><svg width="14" height="14" viewBox="0 0 24 24"><path fill="#c8ccd4" d="M6.6 10.8a15.1 15.1 0 0 0 6.6 6.6l2.2-2.2c.3-.3.7-.4 1-.2 1.1.4 2.3.6 3.6.6.6 0 1 .4 1 1V20c0 .6-.4 1-1 1A17 17 0 0 1 3 4c0-.6.4-1 1-1h3.5c.6 0 1 .4 1 1 0 1.3.2 2.5.6 3.6.1.3 0 .7-.2 1z"/></svg>+1-(888) 555-0142</div>
    <div class="contact-row"><svg width="14" height="14" viewBox="0 0 24 24"><path fill="#c8ccd4" d="M6 3h12v5H6zM3 9h18v9h-3v3H6v-3H3z"/></svg>+1-(888) 555-0142</div>
    <div class="contact-row"><svg width="14" height="14" viewBox="0 0 24 24"><path fill="#c8ccd4" d="M2 5h20v14H2z"/><path fill="none" stroke="#1b2130" stroke-width="2" d="M2 6l10 7 10-7"/></svg>info@brelvanto.com</div>
  </div>

  <h4 class="foot-h" style="left:569px">Location <em>Map</em></h4>
  <div class="foot-rule" style="left:569px;width:299px"></div>
  <div class="abs map" role="img" aria-label="Street map with a pin marking the office location"></div>
  <svg class="abs" style="left:660px;top:110px" width="22" height="30" viewBox="0 0 22 30"><path d="M11 0a11 11 0 0 1 11 11c0 8-11 19-11 19S0 19 0 11A11 11 0 0 1 11 0z" fill="#e53935"/><circle cx="11" cy="11" r="4" fill="#8b1c1a"/></svg>

  <div class="abs foot-brand">Brelvanto</div>
  <div class="abs socials" aria-label="Social profiles"><span></span><span></span><span></span><span></span></div>
</footer>

<div class="copyright">Copyright © 2017 Brelvanto. All Rights Reserved.</div>

</body>
</html>
```